Veltrona Pocket Folder

Create a new pocket folder
An Overview / Background of the Business & Services
We would like a new folder to use when making formal presentations
* The Target Market / Audience you are trying to reach
The target audience are commercial businesses that we are selling group insurance products to
* Design Specifics; any preferences or ideas for Style, Colour, Imagery, etc
We wanted to use the Houston, Texas skyline and create something that was simple, yet modern.
* Do you have an existing website or Facebook page were designers can learn more about your company?
Yes, http://www.veltronagroup.example and we are on Linked-In.
Updates
Project Deadline Extended Reason: We have many people who have to agree. We need to get an answer on the form of the ready art we will receive when we select a designer .Thank you. Added Thursday, April 27, 2017
Industry/Entity Type
Business
Look and feel
Each slider illustrates characteristics of the customer's brand and the style your logo design should communicate.

```html
<!DOCTYPE html>
<html lang="en">
<head>
<meta charset="utf-8">
<title>Veltrona Pocket Folder</title>
<link href="https://fonts.googleapis.com/css2?family=Michroma&family=Open+Sans:wght@400;600&display=swap" rel="stylesheet">
<style>
  :root {
    --stage: #bdbcbd;
    --blue-light: #0096d6;
    --blue-mid: #0077b3;
    --blue-deep: #0a4f82;
    --paper: #ffffff;
    --paper-shade: #eceef0;
    --ink-grey: #6d6e70;
    --accent-blue: #1f9ad6;
    --faint-grey: #e3e5e7;
    --faint-blue: #cfdfe6;
  }
  * { box-sizing: border-box; margin: 0; padding: 0; }
  html, body { width: 1200px; height: 1200px; overflow: hidden; }
  body { background: var(--stage); font-family: "Open Sans", sans-serif; }

  .folder-spread {
    position: absolute; left: 60px; top: 240px;
    width: 1080px; height: 720px; display: flex;
    box-shadow: 0 24px 50px rgba(0,0,0,.25);
  }
  .panel { position: relative; width: 540px; height: 720px; overflow: hidden; }

  .back-cover {
    background: linear-gradient(100deg, var(--blue-mid) 0%, var(--blue-light) 40%, var(--blue-mid) 75%, var(--blue-deep) 100%);
    color: var(--paper);
  }
  .back-brand {
    position: absolute; left: 150px; bottom: 120px;
    display: flex; align-items: center; gap: 12px;
  }
  .brand-square { width: 34px; height: 34px; border-radius: 5px; background: var(--paper); }
  .back-brand .wordmark { font-family: "Michroma", sans-serif; font-size: 30px; color: var(--paper); }
  .back-contact {
    position: absolute; left: 70px; bottom: 44px;
    display: flex; gap: 14px; font-size: 11px; line-height: 1.5;
  }
  .address { text-align: right; padding-right: 14px; border-right: 1px solid rgba(255,255,255,.8); }
  .address strong { font-weight: 600; }
  .channels li { list-style: none; display: flex; align-items: center; gap: 6px; }
  .channels svg { width: 10px; height: 10px; fill: var(--paper); }

  .front-cover {
    background: linear-gradient(160deg, var(--paper) 45%, var(--paper-shade) 100%);
  }
  .front-brand {
    position: absolute; left: 100px; top: 150px;
    display: flex; align-items: center; gap: 14px;
  }
  .front-brand .brand-square { width: 44px; height: 44px; background: var(--accent-blue); }
  .front-brand .wordmark { font-family: "Michroma", sans-serif; font-size: 36px; color: var(--ink-grey); }
  .front-accent { position: absolute; right: 0; bottom: 0; width: 300px; height: 340px; }
</style>
</head>
<body>
  <main class="folder-spread">
    <section class="panel back-cover">
      <div class="back-brand">
        <span class="brand-square"></span>
        <span class="wordmark">Veltrona</span>
      </div>
      <div class="back-contact">
        <address class="address">
          <strong>Veltrona Corporation</strong><br>
          4200 Meridian Park Drive, Suite 310<br>
          Houston, TX 77057
        </address>
        <ul class="channels">
          <li><svg viewBox="0 0 10 10"><path d="M2 0 L4 2 L3 3.5 Q4.5 6 6.5 7 L8 6 L10 8 L8.5 10 Q2 8 0 1.5 Z"/></svg>713-555-0148</li>
          <li><svg viewBox="0 0 10 10"><rect x="0" y="2" width="10" height="6" rx="1"/></svg>info@veltronagroup.example</li>
          <li><svg viewBox="0 0 10 10"><circle cx="5" cy="5" r="4.5"/></svg>www.veltronagroup.example</li>
        </ul>
      </div>
    </section>

    <section class="panel front-cover">
      <div class="front-brand">
        <span class="brand-square"></span>
        <span class="wordmark">Veltrona</span>
      </div>
      <svg class="front-accent" viewBox="0 0 300 340" aria-hidden="true">
        <rect x="30" y="40" width="300" height="320" rx="14" fill="var(--faint-grey)"/>
        <rect x="110" y="20" width="220" height="110" rx="50" fill="var(--faint-blue)"/>
      </svg>
    </section>
  </main>
</body>
</html>
```